MRT Property - Business Cards

Looking for a business card & general letterhead, signage etc design for our new logo.

Colours:
000a20
0056a2
00b5ef
0088ce
68cef2

Fonts:
Poppins
Karla

Please keep look and feel of new brand - example in the zip package I sent.

```html
<!DOCTYPE html>
<html lang="en">
<head>
<meta charset="utf-8">
<title>MRT Property – Letterhead</title>
<link rel="stylesheet" href="https://fonts.googleapis.com/css2?family=Poppins:wght@700&family=Open+Sans:wght@400;700&family=Montserrat:wght@400&display=swap">
<style>
  :root {
    --ink: #000a20;
    --navy: #0056a2;
    --sky: #00b5ef;
    --azure: #0088ce;
    --ice: #68cef2;
    --backdrop: #8c8c8c;
    --paper: #ffffff;
    --signature-tint: #eef2f7;
  }
  * { margin: 0; padding: 0; box-sizing: border-box; }
  html, body { width: 1200px; height: 686px; overflow: hidden; }
  body { background: var(--backdrop); position: relative; }

  .letterhead {
    position: absolute; left: 374px; top: 23px;
    width: 452px; height: 640px;
    background: var(--paper);
    box-shadow: 0 6px 18px rgba(0,0,0,.25);
    overflow: hidden;
    font-family: "Open Sans", Arial, sans-serif;
    color: var(--ink);
  }
  .letterhead__art { position: absolute; inset: 0; }

  .brand {
    position: absolute; left: 30px; top: 46px;
    display: flex; align-items: center; gap: 7px;
    font-family: "Poppins", sans-serif; font-weight: 700;
    font-size: 18px; line-height: 22px; color: var(--navy);
  }
  .brand__dot { width: 13px; height: 13px; border-radius: 50%; background: var(--azure); }

  .contact {
    position: absolute; left: 300px; top: 20px;
    font-family: "Montserrat", sans-serif; font-size: 7.2px; line-height: 11px;
    color: var(--paper); list-style: none;
  }
  .contact li { display: flex; align-items: center; gap: 5px; white-space: nowrap; }
  .contact svg { width: 7px; height: 7px; flex: none; }
  .contact__address { padding-left: 12px; }

  .recipient { position: absolute; left: 22px; top: 155px; font-size: 7.4px; line-height: 10.4px; }
  .recipient__date { margin-bottom: 2px; }
  .recipient__name { font-weight: 700; font-size: 9.4px; line-height: 11px; }

  .letter { position: absolute; left: 22px; top: 244px; width: 404px; font-size: 7.6px; line-height: 11.2px; }
  .letter__salutation { font-weight: 700; font-size: 9.4px; line-height: 12px; margin-bottom: 6px; }
  .letter p { margin-bottom: 10px; }

  .sign-off { position: absolute; left: 22px; top: 488px; }
  .sign-off__signature { width: 110px; height: 24px; background: var(--signature-tint); border-radius: 3px; }
  .sign-off__name { font-weight: 700; font-size: 17px; line-height: 20px; margin-top: 4px; }
  .sign-off__role { font-size: 7.4px; line-height: 10px; }
</style>
</head>
<body>
  <article class="letterhead">
    <svg class="letterhead__art" viewBox="0 0 452 640" aria-hidden="true">
      <path d="M0 0 H452 V124 C400 118 330 112 290 100 C250 88 230 50 200 30 C170 14 100 10 0 8 Z" fill="var(--navy)"/>
      <path d="M0 13 C100 15 170 19 198 35 C228 55 248 93 288 105 C328 117 400 123 452 129" fill="none" stroke="var(--ice)" stroke-width="3.5"/>
      <path d="M0 19 C100 21 168 25 195 41 C225 61 245 99 286 111 C326 123 400 129 452 135" fill="none" stroke="var(--sky)" stroke-width="2"/>
      <path d="M0 630 H194 Q200 630 204 640 H0 Z" fill="var(--ice)"/>
      <path d="M206 628 H452 V640 H214 Z" fill="var(--navy)"/>
    </svg>

    <div class="brand"><span class="brand__dot"></span>MRT Property</div>

    <ul class="contact">
      <li><svg viewBox="0 0 10 10"><path d="M2 1 L4 1 L5 3.5 L3.8 4.5 Q5 6.5 6 6.8 L7 5.5 L9.5 6.5 V8.5 Q9 9.5 8 9.5 Q1 9 0.5 2 Q0.5 1 2 1Z" fill="var(--ice)"/></svg>+61 2 9000 4821</li>
      <li><svg viewBox="0 0 10 10"><circle cx="5" cy="5" r="4" fill="none" stroke="var(--ice)" stroke-width="1.2"/><path d="M1 5 H9 M5 1 V9" stroke="var(--ice)" stroke-width=".8"/></svg>www.mrtproperty.com.au</li>
      <li><svg viewBox="0 0 10 10"><rect x="0.5" y="2" width="9" height="6.5" fill="none" stroke="var(--ice)" stroke-width="1.2"/><path d="M0.5 2 L5 6 L9.5 2" fill="none" stroke="var(--ice)" stroke-width="1"/></svg>info@mrtproperty.com.au</li>
      <li><svg viewBox="0 0 10 10"><path d="M5 9.5 C2 6 1.5 4.5 1.5 3.5 A3.5 3.5 0 0 1 8.5 3.5 C8.5 4.5 8 6 5 9.5Z" fill="var(--ice)"/><circle cx="5" cy="3.5" r="1.2" fill="var(--navy)"/></svg>Suite 4.12, Level 4</li>
      <li class="contact__address">18 Harbour View Road</li>
      <li class="contact__address">Rhodes Park NSW 2138</li>
    </ul>

    <div class="recipient">
      <p class="recipient__date">August-05-2019</p>
      <p class="recipient__name">Clara Weston</p>
      <p>Director</p>
      <p>730 Maple Grove Rd. Suite 120</p>
      <p>Austin, TX 78701</p>
    </div>

    <section class="letter">
      <h2 class="letter__salutation">Clara Weston</h2>
      <p>Lorem ipsum dolor sit amet, consectetuer adipiscing elit, sed diam nonummy nibh euismod tincidunt ut laoreet dolore magna aliquam erat volutpat. Ut wisi enim ad minim veniam, quis nostrud exerci tation ullamcorper suscipit lobortis</p>
      <p>Lorem ipsum dolor sit amet, cons ectetuer adipiscing elit, sed diam nonummy nibh euismod tincidunt ut laoreet dolore magna aliquam erat volutpat. Ut wisi enim ad minim veniam, quis nostrud exerci tation ullamcorper suscipit lobortis nisl ut aliquip ex ea commodo consequat. Lorem ipsum dolor sit amet, consectetuer olutpat. Ut wisi enim ad minim veniam, quis nostrud exerci tation ullamcorper suscipit lobortis nisl ut aliquip ex ea commodo consequat. Duis autem</p>
      <p>vel eum iriure dolor in hendrerit in vulputate velit esse molestie consequat, vel illum dolore eu feugiat nulla facilisis at vero eros et accumsan et iusto odio dignissim qui blandit praesent luptatum zzril delenit augue duis dolore te feugait nulla facilisi. Lorem ipsum dolor sit amet, cons ectetuer adipiscing elit, sed diam nonummy nibh euismod tincidunt ut laoreet dolore magna aliquam erat volutpat. Ut wisi enim.</p>
    </section>

    <div class="sign-off">
      <div class="sign-off__signature" role="img" aria-label="Handwritten signature"></div>
      <p class="sign-off__name">Daniel Reeve</p>
      <p class="sign-off__role">Co-Founder</p>
    </div>
  </article>
</body>
</html>
```